Book cover for a New Adult, romance/ contemporary novel.

I need a full front, back, and spine cover for my upcoming book. The novel is a romance/ coming of age book and is similar to Every Quiet Harbor by Margot Ellsby. My main audience is women in their late teens/ early 20's. The book is an emotional, reminiscent piece and I would love to see some cover designs with a darker palette like Waiting on Tuesday, Nine Rooms Over, or Bartholomew and Felix (but I also adore some lighter covers, especially those that feature the couple such as Any Later Day or Past Each Dusk). Feel free to send some minimal designs as well if you have any! A great idea of that would be the cover for Salt and Clover or Waiting on Tuesday. If you go with a minimal design, I'd love to see silhouettes or maybe a burning candle. Another possible idea I thought of would be a scene at a concert with the crowd silhouetted and then my main character (more details on her below) standing in the middle of it all. I prefer animation/drawing etc over real models. But feel free to send me whatever you think might match the vibe, I'd love to see anything you have in mind! Some main symbols in my book are stars and candles. The main character (Hannah) is a female Korean with brown, medium length straight hair, and the love interest (Colin) is a tall and thin male Caucasian with curly brown hair. The book is openly emotional, wistful, and sets an ache in your chest, so I can't wait to see what designs you artists come up with! (My barcode will need to be included on the back cover, and I am getting that soon!)
The title is "The Weight of Mornings" and the author's name is Priya Holcomb. The book's dimensions will be 5.5x8.25. The blurb for the back cover is:
When happily ever falls apart, all you can do is move forward… and reminisce. Hannah Mio returns home from college following a tragic incident she can’t bring herself to talk about and a breakup with her boyfriend, Colin Phelps. Finding it difficult to confront her traumas, she begins therapy. Hannah takes the therapist on a rollercoaster journey of her college life, retelling the events that caused her relationship to spiral out of control and led to her dropping out of pre-med despite that being her life-long dream. Hannah sets out to remember how things were before everything got so messed up, and figure out how to continue living now that they are.
The author bio for the back cover is:
Priya Holcomb is the author of A Hollow Sort of Spring. She is a self published writer from Las Vegas who likes to pretend she’s currently in a New York bookstore, drinking a latte, while listening to a carefully curated playlist. When she’s not writing, Priya is taking care of her plant babies and cuddling with the cutest puppy in the world.

```html
<!DOCTYPE html>
<html lang="en">
<head>
<meta charset="utf-8">
<title>The Weight of Mornings — Full Cover</title>
<link rel="stylesheet" href="https://fonts.googleapis.com/css2?family=EB+Garamond:wght@400;500&display=swap">
<style>
  :root {
    --ink: #4e3a44;
    --cream: #f6e2cc;
    --cream-soft: rgba(246, 226, 204, 0.9);
    --fur-light: #efe3d3;
    --fur-mid: #dccab3;
    --shirt: #f3ebea;
    --shirt-shade: #e6d8d6;
    --hair: #35252a;
    --hair-mid: #5c444a;
    --barcode-box: #ffffff;
  }
  * { margin: 0; padding: 0; box-sizing: border-box; }
  html, body { width: 1200px; height: 897px; overflow: hidden; background: var(--cream); }
  .cover {
    position: relative;
    width: 1200px;
    height: 897px;
    overflow: hidden;
    font-family: "EB Garamond", Garamond, serif;
    color: var(--ink);
    background: linear-gradient(120deg, var(--fur-light) 0%, var(--fur-mid) 50%, var(--fur-light) 100%);
  }
  .front-photo {
    position: absolute;
    left: 480px;
    top: 0;
    width: 720px;
    height: 897px;
    background: linear-gradient(158deg,
      var(--shirt) 0%,
      var(--shirt) 28%,
      var(--shirt-shade) 38%,
      var(--hair-mid) 50%,
      var(--hair) 62%,
      var(--hair) 78%,
      var(--hair-mid) 88%,
      var(--fur-mid) 100%);
    -webkit-mask-image: linear-gradient(90deg, transparent 0%, #000 30%);
    mask-image: linear-gradient(90deg, transparent 0%, #000 30%);
  }
  .back-wash {
    position: absolute;
    inset: 0;
    background: linear-gradient(90deg, var(--cream-soft) 0%, var(--cream-soft) 46%, rgba(246,226,204,0.55) 54%, rgba(246,226,204,0) 62%);
  }
  .back-title {
    position: absolute;
    left: 0;
    width: 588px;
    top: 158px;
    text-align: center;
    font-size: 45px;
    font-weight: 400;
    line-height: 1;
  }
  .blurb {
    position: absolute;
    left: 65px;
    top: 210px;
    width: 455px;
    font-size: 20.4px;
    line-height: 21.7px;
    text-align: justify;
  }
  .candle-mark {
    position: absolute;
    left: 262px;
    top: 487px;
    width: 62px;
    height: 70px;
    border-radius: 6px;
    background: linear-gradient(0deg, rgba(46,30,34,0.55) 0%, rgba(46,30,34,0.12) 100%);
  }
  .author-bio {
    position: absolute;
    left: 69px;
    top: 580px;
    width: 448px;
    font-size: 20px;
    line-height: 21.7px;
    text-align: justify;
  }
  .barcode-space {
    position: absolute;
    left: 347px;
    top: 736px;
    width: 206px;
    height: 122px;
    background: var(--barcode-box);
  }
  .spine {
    position: absolute;
    left: 566px;
    top: 130px;
    width: 64px;
    height: 600px;
  }
  .spine-text {
    position: absolute;
    left: 0;
    top: 0;
    transform-origin: 0 0;
    transform: translate(64px, 0) rotate(90deg);
    white-space: nowrap;
    display: flex;
    align-items: baseline;
    width: 600px;
    height: 64px;
    line-height: 64px;
  }
  .spine-title { font-size: 41px; }
  .spine-author { font-size: 29px; letter-spacing: 2px; margin-left: 46px; }
  .front-author {
    position: absolute;
    left: 700px;
    width: 410px;
    top: 70px;
    text-align: center;
    font-size: 31px;
    letter-spacing: 2.5px;
  }
  .front-title {
    position: absolute;
    left: 690px;
    width: 430px;
    top: 117px;
    text-align: center;
    font-size: 44px;
    font-weight: 500;
    line-height: 1;
    white-space: nowrap;
  }
</style>
</head>
<body>
<main class="cover">
  <div class="front-photo" role="img" aria-label="Photograph of a young woman with long dark hair in a white shirt lying on a cream fur rug, wrapping across the front and spine"></div>
  <div class="back-wash"></div>

  <section class="back-cover">
    <h2 class="back-title">The Weight of Mornings</h2>
    <p class="blurb">When happily ever falls apart, all you can do is move forward… and reminisce. Hannah Mio returns home from college following a tragic incident she can’t bring herself to talk about and a breakup with her boyfriend, Colin Phelps. Finding it difficult to confront her traumas, she begins therapy. Hannah takes the therapist on a rollercoaster journey of her college life, retelling the events that caused her relationship to spiral out of control and led to her dropping out of pre-med despite that being her life-long dream. Hannah sets out to remember how things were before everything got so messed up, and figure out how to continue living now that they are.</p>
    <div class="candle-mark" role="img" aria-label="Small black candle emblem"></div>
    <p class="author-bio">Priya Holcomb is the author of A Hollow Sort of Spring. She is a self published writer from Las Vegas who likes to pretend she’s currently in a New York bookstore, drinking a latte, while listening to a carefully curated playlist. When she’s not writing, Priya is taking care of her plant babies and cuddling with the cutest puppy in the world.</p>
    <div class="barcode-space" aria-label="Reserved barcode area"></div>
  </section>

  <section class="spine">
    <div class="spine-text">
      <span class="spine-title">The Weight of Mornings</span>
      <span class="spine-author">Priya Holcomb</span>
    </div>
  </section>

  <section class="front-cover">
    <p class="front-author">Priya Holcomb</p>
    <h1 class="front-title">The Weight of Mornings</h1>
  </section>
</main>
</body>
</html>
```